Corporate-Design für Steuerberatungsgesellschaft
Zielgruppe
Wir sind eine Steuerberatungsgesellschaft mit 10 Mitarbeitern im Norden von Deutschland, kurz vor der Ostseeküste. Unser Unternehmen besteht seit 30 Jahren. Wir betreuen vor allem Mandanten in kleinen und mittleren Unternehmen: von der Arztpraxis bis zum Bauunternehmen. Demnächst werden wir neue Räume beziehen. Diese sollen großzügiger und moderner werden, teilweise mit Glaswänden.
Aufgabenstellung
Unser bisheriges Farbkonzept war von bordeaux und creme geprägt (www.kanzlei-mervato.de). Das muss aber nicht weiter bestehen. Das bisherige Logo finden wir inhaltlich recht treffend, aber es sollte moderner gestaltet werden. Der Schriftzug des Kanzleinamens soll an der Fassade in silbernen Buchstaben angebracht werden.

```html
<!DOCTYPE html>
<html lang="de">
<head>
<meta charset="utf-8">
<title>Mervato Steuerberatung – Corporate Design</title>
<link href="https://fonts.googleapis.com/css2?family=Poppins:wght@400;500;600;700&display=swap" rel="stylesheet">
<style>
  :root {
    --bordeaux: #9b1b2a;
    --bordeaux-dark: #7e1520;
    --anthracite: #404547;
    --ink: #3a3f41;
    --paper: #ffffff;
    --stage-grey: #b9b9bd;
    --stage-mint: #e6ebe7;
    --muted: #5a5f61;
  }
  * { box-sizing: border-box; margin: 0; padding: 0; }
  html, body { width: 1200px; height: 2416px; overflow: hidden; }
  body { font-family: "Poppins", sans-serif; color: var(--ink); background: var(--paper); position: relative; }

  .section { position: absolute; left: 0; width: 1200px; }
  .section--logo { top: 0; height: 570px; background: var(--paper); }
  .section--cards { top: 570px; height: 765px; background: var(--stage-grey); }
  .section--letter { top: 1335px; height: 1081px; background: var(--stage-mint); }

  /* Wordmark */
  .wordmark { position: absolute; display: flex; align-items: center; gap: 14px; }
  .wordmark__square { width: 1em; height: 1em; background: var(--bordeaux); flex: none; }
  .wordmark__text { display: flex; flex-direction: column; line-height: 1; }
  .wordmark__name { font-weight: 600; color: var(--ink); letter-spacing: .04em; }
  .wordmark__sub { font-weight: 500; color: var(--ink); letter-spacing: .62em; margin-top: .4em; }

  .section--logo .wordmark { left: 280px; top: 228px; font-size: 108px; }
  .section--logo .wordmark__name { font-size: 86px; }
  .section--logo .wordmark__sub { font-size: 19px; }

  /* Business cards */
  .card { position: absolute; width: 440px; height: 260px; box-shadow: 0 12px 24px rgba(0,0,0,.18); overflow: hidden; }
  .card--front { left: 80px; top: 250px; background: var(--anthracite); }
  .card--back { left: 680px; top: 250px; background: var(--paper); }
  .card__stripe { position: absolute; left: 0; right: 0; bottom: 22px; height: 6px; background: var(--bordeaux); }
  .card__ghost { position: absolute; right: 28px; top: 24px; width: 130px; height: 130px; background: rgba(255,255,255,.05); }
  .card--front .wordmark { left: 72px; top: 98px; font-size: 44px; gap: 10px; }
  .card--front .wordmark__name { color: #fff; font-size: 36px; }
  .card--front .wordmark__sub { color: #fff; font-size: 9px; }
  .card__mark-plain { position: absolute; left: 26px; bottom: 40px; width: 110px; height: 110px; background: var(--bordeaux); }
  .card__person { position: absolute; left: 26px; top: 24px; }
  .card__title { font-size: 12px; color: var(--muted); }
  .card__name { font-size: 19px; font-weight: 700; color: var(--bordeaux); line-height: 1.2; }
  .card__role { font-size: 12px; color: var(--muted); }
  .card__contact { position: absolute; left: 200px; top: 24px; font-size: 10.5px; line-height: 1.6; color: var(--ink); }
  .card__contact .accent { color: var(--bordeaux); }
  .card__contact ul { list-style: none; margin-top: 10px; }

  .icon-dot { display: inline-block; width: 9px; height: 9px; border-radius: 50%; background: var(--bordeaux); margin-right: 8px; vertical-align: -1px; }

  /* Letterhead */
  .letterhead { position: absolute; left: 348px; top: 160px; width: 542px; height: 770px; background: #f4f4f4; box-shadow: 0 40px 60px rgba(0,0,0,.22); overflow: hidden; }
  .letterhead .wordmark { left: 288px; top: 28px; font-size: 38px; gap: 8px; }
  .letterhead .wordmark__name { font-size: 30px; }
  .letterhead .wordmark__sub { font-size: 7.5px; }
  .letterhead__sender { position: absolute; left: 58px; top: 123px; font-size: 6.5px; line-height: 1.6; }
  .letterhead__sender strong { font-weight: 600; }
  .letterhead__sender-rule { position: absolute; left: 0; top: 146px; width: 176px; height: 2px; background: var(--bordeaux); }
  .letterhead__contact { position: absolute; left: 352px; top: 114px; list-style: none; font-size: 8.5px; line-height: 1.58; }
  .letterhead__contact .icon-dot { width: 8px; height: 8px; }
  .letterhead__contact-rule { position: absolute; left: 352px; top: 176px; width: 190px; height: 2px; background: var(--bordeaux); }
  .letterhead__directors { position: absolute; left: 352px; top: 186px; font-size: 8.5px; line-height: 1.6; }
  .letterhead__directors strong { font-weight: 600; }
  .letterhead__footer { position: absolute; left: 0; bottom: 0; width: 380px; height: 66px; background: var(--bordeaux-dark); color: #fff; font-size: 6.5px; line-height: 2.45; padding: 10px 0 0 54px; }
  .letterhead__footer strong { font-weight: 600; }
  .letterhead__mark-plain { position: absolute; right: 0; bottom: 0; width: 150px; height: 126px; background: var(--anthracite); }
</style>
</head>
<body>

<section class="section section--logo">
  <div class="wordmark">
    <span class="wordmark__square"></span>
    <div class="wordmark__text">
      <span class="wordmark__name">MERVATO</span>
      <span class="wordmark__sub">STEUERBERATUNG</span>
    </div>
  </div>
</section>

<section class="section section--cards">
  <div class="card card--front">
    <div class="card__ghost"></div>
    <div class="wordmark">
      <span class="wordmark__square"></span>
      <div class="wordmark__text">
        <span class="wordmark__name">MERVATO</span>
        <span class="wordmark__sub">STEUERBERATUNG</span>
      </div>
    </div>
    <div class="card__stripe"></div>
  </div>

  <div class="card card--back">
    <div class="card__person">
      <p class="card__title">Diplom-Kauffrau</p>
      <p class="card__name">Helga Brandner</p>
      <p class="card__role">Steuerberaterin</p>
    </div>
    <div class="card__contact">
      <p><span class="accent">Mervato</span></p>
      <p>Steuerberatungsgesellschaft mbH</p>
      <p>Lindenstraße 4</p>
      <p>D - 17390 Neustrand</p>
      <ul>
        <li><span class="icon-dot"></span>+49 (0) 3900 / 12 34 - 0</li>
        <li><span class="icon-dot"></span>+49 (0) 3900 / 12 34 - 49</li>
        <li><span class="icon-dot"></span>info@kanzlei-mervato.de</li>
        <li><span class="icon-dot"></span>www.kanzlei-mervato.de</li>
      </ul>
    </div>
    <div class="card__mark-plain"></div>
    <div class="card__stripe"></div>
  </div>
</section>

<section class="section section--letter">
  <div class="letterhead">
    <div class="wordmark">
      <span class="wordmark__square"></span>
      <div class="wordmark__text">
        <span class="wordmark__name">MERVATO</span>
        <span class="wordmark__sub">STEUERBERATUNG</span>
      </div>
    </div>

    <div class="letterhead__sender">
      <p><strong>Mervato Steuerberatungsgesellschaft mbH</strong></p>
      <p>Lindenstraße 4 · D · 17390 Neustrand</p>
    </div>
    <div class="letterhead__sender-rule"></div>

    <ul class="letterhead__contact">
      <li><span class="icon-dot"></span>+49 (0) 3900 / 12 34-0</li>
      <li><span class="icon-dot"></span>+49 (0) 3900 / 12 34-49</li>
      <li><span class="icon-dot"></span>info@kanzlei-mervato.de</li>
      <li><span class="icon-dot"></span>www.kanzlei-mervato.de</li>
    </ul>
    <div class="letterhead__contact-rule"></div>

    <div class="letterhead__directors">
      <p>Geschäftsführer:</p>
      <p><strong>Lars Vettermann</strong></p>
      <p>Steuerberater / Dipl. Kaufmann</p>
      <p><strong>Jens Olbrich</strong></p>
      <p>Steuerberater</p>
    </div>

    <div class="letterhead__footer">
      <p><strong>Mervato Steuerberatungsgesellschaft mbH</strong> · Lindenstraße 4 · D · 17390 Neustrand</p>
      <p><strong>USt-IdNr.</strong> DE000000000 · AG Neustrand · HRB 4718</p>
      <p>Sparkasse Neustrand · <strong>IBAN</strong> DE00 0000 0000 0000 0000 00 · <strong>BIC</strong> NEUSDE21XXX</p>
    </div>
    <div class="letterhead__mark-plain"></div>
  </div>
</section>

</body>
</html>
```